Stationery for a private security company, "Brenmoor Security Services Ltd."

Needed is a stationery design for a private security company. The designs must show professionalism and that our company mean nothing but business. Watermark of the company logo on the letterhead page is also a must. The final design must represent innovation and professionalism. It would be great if designers could integrate the colours black and silver onto the cards and letterheads..

Thank you

```html
<!DOCTYPE html>
<html lang="en">
<head>
<meta charset="utf-8">
<title>Brenmoor Security Services Ltd. — Stationery</title>
<link href="https://fonts.googleapis.com/css2?family=Open+Sans:wght@400;600;700&display=swap" rel="stylesheet">
<style>
  :root {
    --page: #ffffff;
    --charcoal: #3c3c3e;
    --graphite: #2a2a2c;
    --silver: #c9c9cb;
    --silver-light: #e6e6e8;
    --ink: #1e1e20;
    --paper: #ffffff;
    --shadow: rgba(0, 0, 0, 0.55);
  }
  * { margin: 0; padding: 0; box-sizing: border-box; }
  html, body { width: 1200px; height: 848px; overflow: hidden; background: var(--page); }
  body { position: relative; font-family: "Open Sans", Arial, sans-serif; color: var(--ink); }

  .sheet { position: absolute; background: var(--paper); box-shadow: 6px 7px 7px var(--shadow); overflow: hidden; }
  .sheet svg.art { position: absolute; inset: 0; width: 100%; height: 100%; }

  .wordmark { position: absolute; font-weight: 700; color: var(--graphite); line-height: 1.05; text-align: center; }
  .wordmark .name { display: block; letter-spacing: 0.06em; }
  .wordmark .sub { display: block; }

  /* Business card */
  .card { left: 190px; top: 199px; width: 221px; height: 134px; }
  .card .wordmark { left: 6px; top: 42px; width: 76px; }
  .card .wordmark .name { font-size: 10px; }
  .card .wordmark .sub { font-size: 4.6px; }
  .card .holder { position: absolute; right: 6px; top: 31px; text-align: center; color: var(--ink); }
  .card .holder .person { font-size: 11px; font-weight: 400; letter-spacing: 0.02em; text-transform: uppercase; }
  .card .holder .person .family { font-size: 8.5px; }
  .card .holder .role { font-size: 7.5px; margin-top: 1px; }
  .card .contact { position: absolute; left: 46px; top: 104px; font-size: 5.4px; line-height: 1.6; color: var(--ink); }

  /* Letterhead */
  .letterhead { left: 661px; top: 84px; width: 517px; height: 730px; border: 1px solid var(--graphite); }
  .letterhead .wordmark { left: 6px; top: 66px; width: 120px; }
  .letterhead .wordmark .name { font-size: 15px; }
  .letterhead .wordmark .sub { font-size: 6.6px; }
  .letterhead .contact { position: absolute; right: 42px; top: 80px; font-size: 10.5px; line-height: 1.6; text-align: right; }
  .letterhead .phone { position: absolute; right: 16px; bottom: 9px; font-size: 10.5px; }

  /* Envelope */
  .envelope { left: 43px; top: 541px; width: 566px; height: 243px; border: 1px solid var(--graphite); }
  .envelope .wordmark { left: 6px; top: 57px; width: 120px; }
  .envelope .wordmark .name { font-size: 15px; }
  .envelope .wordmark .sub { font-size: 6.6px; }
  .envelope .contact { position: absolute; left: 27px; top: 220px; font-size: 6.8px; line-height: 1.45; }
</style>
</head>
<body>

<section class="sheet card" aria-label="Business card">
  <svg class="art" viewBox="0 0 221 134" preserveAspectRatio="none" aria-hidden="true">
    <defs>
      <linearGradient id="cardBase" x1="0" y1="0" x2="1" y2="1">
        <stop offset="0" stop-color="#3a3a3c"/>
        <stop offset="1" stop-color="#555557"/>
      </linearGradient>
      <linearGradient id="cardFacet" x1="0" y1="0" x2="1" y2="0.4">
        <stop offset="0" stop-color="#3c3c3e"/>
        <stop offset="0.55" stop-color="#8c8c8e"/>
        <stop offset="1" stop-color="#e2e2e4"/>
      </linearGradient>
      <linearGradient id="cardFacet2" x1="0" y1="0" x2="1" y2="1">
        <stop offset="0" stop-color="#6a6a6c"/>
        <stop offset="1" stop-color="#f0f0f2"/>
      </linearGradient>
    </defs>
    <rect width="221" height="134" fill="url(#cardBase)"/>
    <polygon points="0,134 117,31 221,31 221,134" fill="url(#cardFacet)"/>
    <polygon points="117,31 221,134 221,31" fill="url(#cardFacet2)" opacity="0.55"/>
  </svg>
  <div class="wordmark"><span class="name">BRENMOOR</span><span class="sub">Security Services Ltd.</span></div>
  <div class="holder">
    <p class="person">Arlen <span class="family">Voss</span></p>
    <p class="role">President</p>
  </div>
  <div class="contact">
    <p>add. : 214/3, Kestrel Lane, North Quarry Road, Hollowmere</p>
    <p>www.brenmoorltd.com,&nbsp; arlen@brenmoor.com</p>
    <p>ph. 77 77 77 77 77</p>
  </div>
</section>

<section class="sheet letterhead" aria-label="Letterhead">
  <svg class="art" viewBox="0 0 517 730" preserveAspectRatio="none" aria-hidden="true">
    <defs>
      <linearGradient id="lhTop" x1="0" y1="0" x2="1" y2="0">
        <stop offset="0" stop-color="#3a3a3c"/>
        <stop offset="1" stop-color="#4a4a4c"/>
      </linearGradient>
      <linearGradient id="lhFoot" x1="0" y1="1" x2="1" y2="0">
        <stop offset="0" stop-color="#1e1e20"/>
        <stop offset="0.6" stop-color="#6a6a6c"/>
        <stop offset="1" stop-color="#d6d6d8"/>
      </linearGradient>
      <linearGradient id="lhFacet" x1="0" y1="0" x2="1" y2="1">
        <stop offset="0" stop-color="#5a5a5c"/>
        <stop offset="1" stop-color="#f2f2f4"/>
      </linearGradient>
    </defs>
    <polygon points="0,0 517,0 517,2 164,53 0,197" fill="url(#lhTop)"/>
    <polygon points="0,730 327,586 517,563 517,730" fill="url(#lhFoot)"/>
    <polygon points="327,586 517,563 517,700" fill="url(#lhFacet)" opacity="0.5"/>
  </svg>
  <div class="wordmark"><span class="name">BRENMOOR</span><span class="sub">Security Services Ltd.</span></div>
  <div class="contact">
    <p>add. :&nbsp; 214/3, Kestrel Lane, North Quarry Road,&nbsp; Hollowmere</p>
    <p>www.brenmoorltd.com,&nbsp; arlen@brenmoor.com</p>
  </div>
  <p class="phone">ph. 77 77 77 77 77</p>
</section>

<section class="sheet envelope" aria-label="Envelope">
  <svg class="art" viewBox="0 0 566 243" preserveAspectRatio="none" aria-hidden="true">
    <defs>
      <linearGradient id="envTop" x1="0" y1="0" x2="1" y2="0">
        <stop offset="0" stop-color="#3a3a3c"/>
        <stop offset="1" stop-color="#4a4a4c"/>
      </linearGradient>
    </defs>
    <polygon points="0,0 566,0 566,3 132,46 0,243" fill="url(#envTop)"/>
    <polygon points="566,216 553,231 545,243 566,243" fill="#3a3a3c"/>
  </svg>
  <div class="wordmark"><span class="name">BRENMOOR</span><span class="sub">Security Services Ltd.</span></div>
  <div class="contact">
    <p>add. :&nbsp; 214/3, Kestrel Lane, North Quarry Road,&nbsp; Hollowmere</p>
    <p>www.brenmoorltd.com,&nbsp; arlen@brenmoor.com,&nbsp; ph. 77 77 77 77 77</p>
  </div>
</section>

</body>
</html>
```